Vegan bakery needs business card

We need a business card design for my vegan bakery in Philadelphia Pa. We create amazing whole food plant based cuisine that is egg and dairy free. We use fruits, vegetables, healing herbs, nuts, natural sugars (date, turbinado, agave) and non bleached flours in our creations. Due to demand and interest in the Philadelphia area we created a late night vegan dessert delivery service named Bramble Vegan. We are the only business providing delicious vegan desserts delivered to your door at 1am!! We would like to see designs that use the color scheme in the logo. The final design should communicate the benefits of our products: dairy/egg free, plant based, healing herbs, amazing food.

```html
<!DOCTYPE html>
<html lang="en">
<head>
<meta charset="utf-8">
<title>Bramble Vegan – Business Card</title>
<link href="https://fonts.googleapis.com/css2?family=Questrial&display=swap" rel="stylesheet">
<style>
  :root {
    --salmon: #ec7b6a;
    --green: #6cbf3c;
    --charcoal: #58595b;
    --white: #ffffff;
    --backdrop: #e6e6e6;
    --card-w: 660px;
    --card-h: 377px;
  }
  * { box-sizing: border-box; margin: 0; padding: 0; }
  html, body {
    width: 1200px; height: 880px; overflow: hidden;
    background: var(--backdrop);
    font-family: "Questrial", "Century Gothic", sans-serif;
  }
  .sheet {
    width: 1200px; height: 880px;
    display: flex; flex-direction: column; align-items: center; justify-content: center;
    gap: 40px;
  }
  .card {
    position: relative;
    width: var(--card-w); height: var(--card-h);
    background: var(--white);
    border-radius: 22px;
    overflow: hidden;
    box-shadow: 0 6px 18px rgba(0,0,0,.18);
  }

  /* brand block */
  .brand { position: absolute; text-align: center; }
  .brand-name {
    display: flex; align-items: center; justify-content: center; gap: 10px;
    color: var(--salmon); font-size: 38px; letter-spacing: .5px; white-space: nowrap;
  }
  .brand-dot {
    width: 18px; height: 18px; border-radius: 50%; background: var(--salmon);
  }
  .tagline {
    margin-top: 8px; color: var(--green); font-size: 22px; line-height: 1.05;
  }

  /* front */
  .card-front .brand { left: 0; right: 0; top: 86px; }
  .products {
    position: absolute; left: 0; right: 0; top: 262px;
    display: flex; align-items: center; gap: 12px;
  }
  .products-rule { flex: 1; height: 1.5px; background: var(--green); }
  .products-label { color: var(--green); font-size: 17px; letter-spacing: .5px; }
  .products-list {
    position: absolute; left: 0; right: 0; top: 290px;
    text-align: center; color: var(--salmon); font-size: 19px;
  }

  /* back */
  .swoosh { position: absolute; inset: 0; }
  .card-back .brand { left: 56px; top: 104px; }
  .card-back .brand-name { font-size: 32px; }
  .card-back .tagline { font-size: 19px; }
  .holder { position: absolute; right: 34px; top: 30px; text-align: right; }
  .holder-name { color: var(--salmon); font-size: 24px; }
  .holder-title { color: var(--charcoal); font-size: 16px; margin-top: 2px; }
  .contact {
    position: absolute; right: 26px; top: 216px;
    text-align: right; color: var(--white); font-size: 14px; line-height: 1.4;
    font-style: normal;
  }
  .contact-address { margin-bottom: 8px; }
  .contact-line { display: flex; justify-content: flex-end; align-items: center; gap: 8px; }
  .contact-icon { width: 16px; height: 16px; flex: none; }
</style>
</head>
<body>
<main class="sheet">

  <section class="card card-front" aria-label="Card front">
    <div class="brand">
      <div class="brand-name"><span class="brand-dot"></span>Bramble Vegan</div>
      <p class="tagline">100% vegan<br>100% delicious</p>
    </div>
    <div class="products">
      <span class="products-rule"></span>
      <span class="products-label">OUR PRODUCTS</span>
      <span class="products-rule"></span>
    </div>
    <p class="products-list">dairy/egg free, plant based, healing herbs, amazing food.</p>
  </section>

  <section class="card card-back" aria-label="Card back">
    <svg class="swoosh" viewBox="0 0 660 377" aria-hidden="true">
      <path d="M0,318 C190,322 300,290 360,200 C320,296 200,342 0,344 Z" fill="var(--salmon)"/>
      <path d="M660,110 C540,110 480,160 430,235 C385,305 330,352 230,377 L660,377 Z" fill="var(--charcoal)"/>
      <path d="M165,377 C290,352 360,305 398,246 C372,310 310,356 205,377 Z" fill="var(--charcoal)"/>
    </svg>

    <div class="brand">
      <div class="brand-name"><span class="brand-dot"></span>Bramble Vegan</div>
      <p class="tagline">100% vegan<br>100% delicious</p>
    </div>

    <div class="holder">
      <p class="holder-name">Nora Castell</p>
      <p class="holder-title">Director of Marketing</p>
    </div>

    <address class="contact">
      <p class="contact-address">Po Box 48, Orchard Lane<br>Dover, DE 19901</p>
      <p class="contact-line">555-218-4470
        <svg class="contact-icon" viewBox="0 0 16 16" aria-label="Phone"><circle cx="8" cy="8" r="8" fill="var(--white)"/><path d="M5 4.5c.5-.5 1-.4 1.3 0l.8 1.2c.2.4.1.8-.2 1l-.5.4c.4.9 1.1 1.6 2 2l.4-.5c.3-.3.7-.4 1-.2l1.2.8c.4.3.5.8 0 1.3-.6.6-1.4.8-2.3.4C7 10.2 5.8 9 5 7.3c-.4-.9-.6-2.2 0-2.8z" fill="var(--charcoal)"/></svg>
      </p>
      <p class="contact-line">hello@bramblevegan.com
        <svg class="contact-icon" viewBox="0 0 16 16" aria-label="Email"><circle cx="8" cy="8" r="8" fill="var(--white)"/><rect x="4" y="5" width="8" height="6" fill="none" stroke="var(--charcoal)" stroke-width="1.2"/><path d="M4 5l4 3.2L12 5" fill="none" stroke="var(--charcoal)" stroke-width="1.2"/></svg>
      </p>
      <p class="contact-line">www.bramblevegan.com
        <svg class="contact-icon" viewBox="0 0 16 16" aria-label="Website"><circle cx="8" cy="8" r="8" fill="var(--white)"/><circle cx="8" cy="8" r="4.2" fill="none" stroke="var(--charcoal)" stroke-width="1.1"/><ellipse cx="8" cy="8" rx="1.8" ry="4.2" fill="none" stroke="var(--charcoal)" stroke-width="1"/><path d="M3.8 8h8.4" stroke="var(--charcoal)" stroke-width="1"/></svg>
      </p>
    </address>
  </section>

</main>
</body>
</html>
```